TLMWOS - Website Design

We require a WordPress website for an accounting firm.
Please review our concept design found on our development site:
http://quillmarsh.ca/tlmwoxe.
The client would like to carry the look and feel of the National Corporate site http://www.tlm.ca as well.
The site must be mobile ready (responsive)
The client will be providing a collection of staff photos for a contact page
Accounting

```html
<!DOCTYPE html>
<html lang="en">
<head>
<meta charset="utf-8">
<title>TLMWOS – Chartered Professional Accountants</title>
<link rel="stylesheet" href="https://fonts.googleapis.com/css2?family=Cinzel:wght@400;700&family=Open+Sans:wght@400;600;700&family=Oswald:wght@400;500&display=swap">
<style>
:root{
  --page:#2e2f31;
  --white:#ffffff;
  --ink:#333333;
  --muted:#7a7a7a;
  --rule:#e3e3e3;
  --brand:#4a5a3a;
  --red:#b8322a;
  --blue:#2c5f8f;
  --green:#3e8a5c;
  --footer:#252628;
  --footer-ink:#a9a9a9;
  --bottom:#1b1c1d;
}
*{box-sizing:border-box;margin:0;padding:0}
html,body{width:1200px;height:2452px;overflow:hidden}
body{background:var(--page);font-family:"Open Sans",sans-serif;color:var(--ink);font-size:13px;line-height:1.6}
ul{list-style:none}

/* header */
.site-header{height:88px;background:var(--white);display:flex;align-items:center;justify-content:space-between;padding:0 108px}
.brand{display:flex;align-items:center;gap:12px}
.brand-mark{width:40px;height:40px;background:var(--brand)}
.brand-name{font-family:"Cinzel",serif;font-weight:700;font-size:24px;color:var(--brand);line-height:1}
.brand-tag{font-family:"Cinzel",serif;font-size:11px;color:var(--brand);letter-spacing:1px;margin-top:4px}
.main-nav{display:flex;gap:44px;font-size:13px;color:#555}
.main-nav a{color:inherit;text-decoration:none}
.main-nav .active{color:var(--brand);font-weight:600}

/* hero */
.hero{height:420px;position:relative;background:linear-gradient(180deg,#6f8577 0%,#3e5547 45%,#243429 100%);display:flex;flex-direction:column;align-items:center;justify-content:center;color:var(--white);text-align:center}
.hero-title{font-family:"Cinzel",serif;font-size:24px;letter-spacing:2px;margin-top:-40px}
.hero-title strong{display:block;font-size:34px;font-weight:400;letter-spacing:3px;margin-top:4px}
.hero-arrow{position:absolute;top:180px;width:30px;height:30px;border:2px solid rgba(255,255,255,.6);border-radius:50%}
.hero-arrow.prev{left:40px}.hero-arrow.next{right:40px}

/* feature boxes */
.feature-band{height:132px;background:#1f2a22}
.features{width:984px;margin:-48px auto 0;display:flex;position:relative}
.feature{flex:1;height:140px;padding:22px 24px;color:var(--white);display:flex;gap:16px}
.feature.red{background:var(--red)}.feature.blue{background:var(--blue)}.feature.green{background:var(--green)}
.feature svg{flex:none}
.feature h3{font-family:"Oswald",sans-serif;font-weight:500;font-size:18px;letter-spacing:.5px}
.feature p{font-size:11px;line-height:1.5;opacity:.9}
.feature .more{font-size:11px;font-weight:700;margin-top:6px;display:block}

/* main */
.content{width:984px;height:1460px;margin:0 auto;background:var(--white);display:flex;padding:36px 24px 0}
.primary{width:640px}
.sidebar{width:272px;margin-left:28px}
.section-title{font-family:"Oswald",sans-serif;font-weight:500;font-size:15px;text-transform:uppercase;letter-spacing:.5px;padding-bottom:8px;border-bottom:2px solid var(--rule);margin-bottom:16px}
.welcome{display:flex;gap:20px;margin-bottom:30px}
.photo{display:block}
.welcome .photo{width:200px;height:150px;flex:none;background:linear-gradient(135deg,#c9cdd1,#7d8791)}
.welcome p{font-size:12px;color:#555}
.posts{display:grid;grid-template-columns:1fr 1fr;gap:26px 30px}
.post .photo{height:190px;margin-bottom:12px}
.post:nth-child(1) .photo{background:linear-gradient(135deg,#d6dde4,#8b9aa8)}
.post:nth-child(2) .photo{background:linear-gradient(135deg,#c8d4e0,#5d7590)}
.post:nth-child(3) .photo{background:linear-gradient(135deg,#e7e7e7,#9a9a9a)}
.post:nth-child(4) .photo{background:linear-gradient(135deg,#eaeaea,#8e8e8e)}
.post:nth-child(5) .photo{background:linear-gradient(135deg,#dcd4cc,#6e6258)}
.post:nth-child(6) .photo{background:linear-gradient(135deg,#d0d8de,#47586a)}
.post h4{font-size:12px;font-weight:700;text-transform:uppercase;line-height:1.4;margin-bottom:8px}
.post p{font-size:11px;color:#666;line-height:1.55}
.pager{display:flex;justify-content:center;gap:6px;margin-top:34px}
.pager span{min-width:26px;height:26px;border:1px solid #ccc;font-size:11px;display:flex;align-items:center;justify-content:center;padding:0 8px;color:#555}
.pager .current{background:var(--brand);color:#fff;border-color:var(--brand)}

.link-list{margin-bottom:28px}
.link-list li{font-size:12px;color:#555;padding:6px 0 6px 14px;border-bottom:1px solid var(--rule);position:relative}
.link-list li::before{content:"";position:absolute;left:2px;top:13px;width:5px;height:5px;background:var(--brand)}
.event{display:flex;gap:12px;margin-bottom:14px}
.event .photo{width:70px;height:52px;flex:none;background:linear-gradient(135deg,#cfd4d9,#6f7b86)}
.event h5{font-size:11px;font-weight:700;text-transform:uppercase;line-height:1.4}
.event time{font-size:10px;color:var(--muted)}
.about{margin-top:26px}
.about .photo{height:150px;background:linear-gradient(180deg,#a9c3dd,#5d7e9e 60%,#3c4a55);margin-bottom:12px}
.about h5{font-size:12px;font-weight:700;text-transform:uppercase;line-height:1.4}
.about p{font-size:11px;color:#666;margin:6px 0 12px}
.btn{display:inline-block;background:var(--red);color:#fff;font-size:11px;font-weight:700;text-transform:uppercase;padding:8px 16px}
.calendar{margin-top:30px;border:1px solid var(--rule)}
.cal-head{background:var(--brand);color:#fff;display:flex;justify-content:space-between;align-items:center;padding:8px 12px;font-family:"Oswald",sans-serif;font-size:13px}
.cal-head i{width:18px;height:18px;background:var(--red);display:block}
.cal-grid{display:grid;grid-template-columns:repeat(7,1fr);gap:3px;padding:8px}
.cal-grid span{height:26px;display:flex;align-items:center;justify-content:center;font-size:10px;background:#f1f1f1;color:#555}
.cal-grid .dow{background:none;font-weight:700}
.cal-grid .empty{background:none}
.cal-grid .today{background:var(--red);color:#fff}

/* footer */
.site-footer{height:340px;background:var(--footer);margin-top:2px;display:flex;padding:30px 108px 0;gap:40px;color:var(--footer-ink)}
.footer-col h6{font-family:"Oswald",sans-serif;font-weight:500;font-size:14px;color:#fff;text-transform:uppercase;letter-spacing:.5px;margin-bottom:14px}
.footer-col li{font-size:11px;line-height:2}
.footer-col.links{width:230px}
.footer-col.welcome-col{width:250px}
.footer-col.welcome-col .cols{display:flex;gap:30px}
.footer-col.info{width:180px}
.social li{display:flex;align-items:center;gap:10px;margin-bottom:8px}
.social li::before{content:"";width:24px;height:24px;border-radius:50%;background:#444}
.bottom-bar{height:55px;background:var(--bottom);color:#777;font-size:10px;display:flex;align-items:center;justify-content:center}
</style>
</head>
<body>

<header class="site-header">
  <div class="brand">
    <span class="brand-mark"></span>
    <div>
      <div class="brand-name">TLMWOS</div>
      <div class="brand-tag">CHARTERED PROFESSIONAL ACCOUNTANTS</div>
    </div>
  </div>
  <nav class="main-nav">
    <a class="active">Home</a><a>Profile</a><a>Client Services</a><a>Resources</a><a>Contact</a>
  </nav>
</header>

<section class="hero" role="img" aria-label="Misty forested mountain range at dusk">
  <span class="hero-arrow prev"></span><span class="hero-arrow next"></span>
  <h1 class="hero-title">WELCOME AND THANK YOU FOR VISITING<strong>THE TLMWOS</strong></h1>
</section>

<section class="feature-band">
  <div class="features">
    <div class="feature red">
      <svg width="40" height="40" viewBox="0 0 40 40"><rect x="6" y="8" width="28" height="26" fill="none" stroke="#fff" stroke-width="2"/><path d="M6 15h28M13 5v6M27 5v6" stroke="#fff" stroke-width="2"/></svg>
      <div><h3>MY BOOKINGS</h3><p>Lorem ipsum is simply dummy text of the printing and typesetting industry.</p><span class="more">Read More Info ›</span></div>
    </div>
    <div class="feature blue">
      <svg width="40" height="40" viewBox="0 0 40 40"><circle cx="20" cy="14" r="7" fill="none" stroke="#fff" stroke-width="2"/><path d="M7 35c2-9 8-12 13-12s11 3 13 12" fill="none" stroke="#fff" stroke-width="2"/></svg>
      <div><h3>CLIENT SERVICES</h3><p>Lorem ipsum is simply dummy text of the printing and typesetting industry.</p><span class="more">Read More Info ›</span></div>
    </div>
    <div class="feature green">
      <svg width="40" height="40" viewBox="0 0 40 40"><rect x="6" y="8" width="28" height="26" fill="none" stroke="#fff" stroke-width="2"/><path d="M6 15h28M12 21h4M18 21h4M24 21h4M12 27h4M18 27h4" stroke="#fff" stroke-width="2"/></svg>
      <div><h3>EVENTS CALENDAR</h3><p>Lorem ipsum is simply dummy text of the printing and typesetting industry.</p><span class="more">Read More Info ›</span></div>
    </div>
  </div>
</section>

<main class="content">
  <div class="primary">
    <h2 class="section-title">Welcome to TLMWOS</h2>
    <div class="welcome">
      <span class="photo" role="img" aria-label="Accountant working with calculator and documents"></span>
      <p>Please note that, as of November 26, 2012, our firm has relocated to a new office in the city centre. Our team is pleased to welcome you to the new space. Explore our site to learn more about who we are, what we do and how we can help. You will find a profile of our firm and the services we provide, plus tools and resources we have designed to make your financial life easier. We look forward to working with you.</p>
    </div>

    <h2 class="section-title">Recent Posts</h2>
    <div class="posts">
      <article class="post"><span class="photo" role="img" aria-label="Business team meeting at a desk"></span><h4>Lorem ipsum is simply dummy text of<br>the printing</h4><p>Lorem ipsum is simply dummy text of the printing and typesetting industry. Lorem ipsum has been the industry's standard dummy text ever.</p></article>
      <article class="post"><span class="photo" role="img" aria-label="Professionals reviewing a report together"></span><h4>Lorem ipsum is simply dummy text of<br>the printing</h4><p>Lorem ipsum is simply dummy text of the printing and typesetting industry. Lorem ipsum has been the industry's standard dummy text ever.</p></article>
      <article class="post"><span class="photo" role="img" aria-label="Hand writing on financial papers"></span><h4>Lorem ipsum is simply dummy text of<br>the printing</h4><p>Lorem ipsum is simply dummy text of the printing and typesetting industry. Lorem ipsum has been the industry's standard dummy text ever.</p></article>
      <article class="post"><span class="photo" role="img" aria-label="Handshake between business partners"></span><h4>Lorem ipsum is simply dummy text of<br>the printing</h4><p>Lorem ipsum is simply dummy text of the printing and typesetting industry. Lorem ipsum has been the industry's standard dummy text ever.</p></article>
      <article class="post"><span class="photo" role="img" aria-label="Senior businessman in a suit"></span><h4>Lorem ipsum is simply dummy text of<br>the printing</h4><p>Lorem ipsum is simply dummy text of the printing and typesetting industry. Lorem ipsum has been the industry's standard dummy text ever.</p></article>
      <article class="post"><span class="photo" role="img" aria-label="Two people shaking hands in an office"></span><h4>Lorem ipsum is simply dummy text of<br>the printing</h4><p>Lorem ipsum is simply dummy text of the printing and typesetting industry. Lorem ipsum has been the industry's standard dummy text ever.</p></article>
    </div>
    <div class="pager"><span>Prev</span><span class="current">1</span><span>2</span><span>3</span><span>4</span><span>5</span><span>6</span><span>…</span><span>10</span><span>Next</span></div>
  </div>

  <aside class="sidebar">
    <h2 class="section-title">Links</h2>
    <ul class="link-list">
      <li>Categories</li><li>Events Calendar</li><li>Financial Tools</li><li>Info Centre</li><li>Locations</li><li>My Bookings</li><li>Sample Page</li><li>Tags</li><li>Links</li>
    </ul>
    <h2 class="section-title">Latest Event</h2>
    <div class="event"><span class="photo" role="img" aria-label="Event photo"></span><div><h5>Lorem ipsum is simply dummy text</h5><time>Posted on 27 March 2015</time></div></div>
    <div class="event"><span class="photo" role="img" aria-label="Event photo"></span><div><h5>Lorem ipsum is simply dummy text</h5><time>Posted on 27 March 2015</time></div></div>
    <div class="event"><span class="photo" role="img" aria-label="Event photo"></span><div><h5>Lorem ipsum is simply dummy text</h5><time>Posted on 27 March 2015</time></div></div>
    <div class="event"><span class="photo" role="img" aria-label="Event photo"></span><div><h5>Lorem ipsum is simply dummy text</h5><time>Posted on 27 March 2015</time></div></div>
    <div class="about">
      <h2 class="section-title">About TLM</h2>
      <span class="photo" role="img" aria-label="Office tower against a blue sky"></span>
      <h5>Lorem ipsum is simply dummy text of the printing</h5>
      <p>Lorem ipsum is simply dummy text of the printing and typesetting industry. Lorem ipsum has been the industry's standard dummy text ever since.</p>
      <span class="btn">Read more info</span>
    </div>
    <div class="calendar">
      <div class="cal-head"><i></i>APRIL 2015<i></i></div>
      <div class="cal-grid">
        <span class="dow">M</span><span class="dow">T</span><span class="dow">W</span><span class="dow">T</span><span class="dow">F</span><span class="dow">S</span><span class="dow">S</span>
        <span class="empty"></span><span class="empty"></span><span>1</span><span>2</span><span>3</span><span>4</span><span>5</span>
        <span>6</span><span>7</span><span>8</span><span>9</span><span>10</span><span>11</span><span>12</span>
        <span>13</span><span>14</span><span>15</span><span>16</span><span>17</span><span>18</span><span>19</span>
        <span>20</span><span>21</span><span>22</span><span class="today">23</span><span>24</span><span>25</span><span>26</span>
        <span>27</span><span>28</span><span>29</span><span>30</span><span class="empty"></span><span class="empty"></span><span class="empty"></span>
      </div>
    </div>
  </aside>
</main>

<footer class="site-footer">
  <div class="footer-col links">
    <h6>Interesting Links</h6>
    <ul><li>› Here are some interesting links for you</li><li>› Here are some interesting links</li><li>› Here are some interesting links for</li><li>› Here are some interesting</li><li>› Here are some interesting links</li><li>› Here are some interesting links for you</li><li>› Here are some interesting links</li><li>› Here are some interesting links for</li></ul>
  </div>
  <div class="footer-col welcome-col">
    <h6>Welcome</h6>
    <div class="cols">
      <ul><li>Categories</li><li>Client Services</li><li>Contact</li><li>Events Calendar</li><li>Financial Tools</li><li>Home</li><li>Info Centre</li><li>Locations</li></ul>
      <ul><li>My Bookings</li><li>Profile</li><li>Resources</li><li>Sample Page</li><li>Tags</li><li>Links</li></ul>
    </div>
  </div>
  <div class="footer-col info">
    <h6>Information</h6>
    <ul><li>Terms &amp; Conditions</li><li>Privacy Policy</li><li>Disclaimer</li></ul>
  </div>
  <div class="footer-col">
    <h6>Follow Us</h6>
    <ul class="social"><li>Pinecircle</li><li>Notewire</li><li>Streamhall</li><li>Brightpost</li></ul>
  </div>
</footer>
<div class="bottom-bar">© Copyright · 2015 TLMWOS · All rights reserved</div>

</body>
</html>
```